Harlow Mechanical Contractors needs a Website

Create basic website for commercial plumbing and mechanical contractor; to include pictures of works in progress and completed works, description of all services offered and geographical locations and licenses

Target Market(s)

General Contractors, Real Estate Developers, Construction Companies

Industry/Entity Type

Construction

Coding

Coded - Design and coding required

Number of Pages Required

5+ page

• See logo attached to project

Colors
0392cd

```html
<!DOCTYPE html>
<html lang="en">
<head>
<meta charset="utf-8">
<title>Harlow Mechanical Contractors</title>
<link rel="stylesheet" href="https://fonts.googleapis.com/css2?family=Exo+2:wght@600;700&family=Open+Sans:wght@400;600&display=swap">
<style>
:root{
  --brand:#0392cd;
  --navy:#123f6b;
  --navy-deep:#0d2f55;
  --ink:#444b52;
  --white:#ffffff;
  --footer-bar:#eeeeee;
}
*{margin:0;padding:0;box-sizing:border-box}
html,body{width:1200px;height:2503px;overflow:hidden;background:var(--white)}
body{position:relative;font-family:"Open Sans",Arial,sans-serif;color:var(--ink)}
.abs{position:absolute}
.heading{font-family:"Exo 2",Arial,sans-serif;font-weight:700}

.header-band{left:0;top:0;width:1200px;height:401px;background:var(--brand)}
.brand{display:flex;align-items:center;gap:10px}
.brand-dot{width:46px;height:46px;border-radius:50%;flex:none}
.brand-name{font-family:"Exo 2",Arial,sans-serif;font-weight:700;font-size:15px;line-height:16px;text-transform:uppercase}
.site-brand{left:175px;top:17px}
.site-brand .brand-dot{background:var(--white)}
.site-brand .brand-name{color:var(--white)}
.main-nav{left:484px;top:56px;display:flex;gap:30px}
.main-nav a{font-family:"Exo 2",Arial,sans-serif;font-weight:700;font-size:15px;color:var(--white);text-decoration:none;text-transform:uppercase}
.main-nav a.current{color:var(--navy-deep)}

.hero-photo{left:175px;top:117px;width:853px;height:442px;background:radial-gradient(circle at 62% 45%,#c9a070 0%,#8a5a3a 35%,#4a3228 70%,#2b2220 100%)}
.hero-title{left:207px;top:230px;width:280px;height:267px;background:rgba(10,30,50,.88);padding:36px 0 0 18px}
.hero-title span{display:block;font-size:35px;line-height:42px;color:var(--white);text-transform:uppercase}
.hero-title .accent{color:var(--brand);font-size:60px;line-height:62px}
.slider-dots{left:1001px;top:462px;display:flex;flex-direction:column;gap:9px}
.slider-dots i{width:9px;height:9px;border-radius:50%;background:var(--white);opacity:.9}
.slider-dots i.on{background:#222}

.section-title{left:0;width:1200px;text-align:center;font-size:29px;text-transform:uppercase}
.title-offer{top:640px;color:var(--brand)}
.title-provide{top:1283px;color:var(--navy)}

.offer-card{top:718px;width:268px;height:505px;background:var(--brand)}
.offer-photo{position:absolute;left:0;top:0;width:100%;height:295px}
.offer-icon{position:absolute;left:95px;top:113px;width:77px;height:70px;background:var(--navy-deep);display:flex;align-items:center;justify-content:center}
.offer-name{position:absolute;left:0;top:210px;width:100%;text-align:center;color:var(--white);font-size:19px;text-transform:uppercase}
.offer-text{position:absolute;left:18px;top:315px;width:232px;text-align:center;color:var(--white);font-size:11.3px;line-height:19.5px}
.read-more{position:absolute;left:73px;top:449px;width:111px;height:35px;background:var(--navy);color:var(--white);font-size:10px;font-weight:600;display:flex;align-items:center;justify-content:center;text-transform:uppercase}

.service{top:1365px;width:414px}
.service-photo{height:267px;position:relative}
.service-label{position:absolute;left:15px;top:160px;width:222px;height:80px;background:var(--brand);color:var(--white);font-size:28px;line-height:29px;padding:10px 0 0 10px;text-transform:uppercase}
.service-text{margin-top:32px;font-size:11.6px;line-height:19.5px;color:var(--ink)}

.testimonials{left:0;top:1797px;width:1200px;height:406px;background:linear-gradient(90deg,#0e3a68 0%,#154a80 55%,#1d5a94 80%,#12406f 100%)}
.testimonials-title{left:0;top:1843px;width:1200px;text-align:center;color:var(--white);font-size:30px;text-transform:uppercase}
.arrow{top:2003px}
.client-photo{left:230px;top:1961px;width:174px;height:174px;border-radius:50%;border:5px solid var(--brand);background:radial-gradient(circle at 50% 40%,#d8dde2,#7a8896 70%,#3b4a5a)}
.quote{left:484px;top:1960px;display:flex;align-items:center;gap:12px}
.quote-name{font-size:24px;color:var(--white);font-family:"Open Sans",Arial,sans-serif;font-weight:400}
.quote-text{left:484px;top:2016px;width:480px;font-size:11.6px;line-height:20px;color:#e3ecf5}

.footer-brand{left:175px;top:2266px}
.footer-brand .brand-dot{width:66px;height:66px;background:var(--navy)}
.footer-brand .brand-name{color:var(--navy);font-size:16px;line-height:17px}
.footer-list{top:2257px;list-style:none;font-size:10.8px;line-height:24px;color:var(--ink);text-transform:uppercase}
.footer-list li{display:flex;align-items:center;gap:9px}
.footer-list li.indent{padding-left:17px}
.footer-bar{left:0;top:2440px;width:1200px;height:63px;background:var(--footer-bar);display:flex;align-items:center;justify-content:center;font-size:10.5px;color:#333;text-transform:uppercase}
</style>
</head>
<body>

<div class="abs header-band"></div>
<div class="abs brand site-brand">
  <span class="brand-dot"></span>
  <span class="brand-name">Harlow<br>Mechanical<br>Contractors</span>
</div>
<nav class="abs main-nav">
  <a class="current">Home</a><a>About Us</a><a>Services</a><a>Clients</a><a>Testimonials</a><a>Contact Us</a>
</nav>

<div class="abs hero-photo" role="img" aria-label="Hands tightening a brass pipe fitting with an adjustable wrench"></div>
<div class="abs hero-title heading">
  <span class="accent">Harlow</span>
  <span>Mechanical</span>
  <span>Contractors</span>
</div>
<div class="abs slider-dots"><i class="on"></i><i></i><i></i><i></i></div>

<h2 class="abs section-title title-offer heading">What We Offer</h2>

<div class="abs offer-card" style="left:175px">
  <div class="offer-photo" role="img" aria-label="Modern large office interior" style="background:linear-gradient(160deg,#c9ccd0,#8e949a 55%,#4a5058)"></div>
  <div class="offer-icon"><svg width="30" height="28" viewBox="0 0 30 28" fill="#fff"><path d="M15 0 30 7H0z"/><rect x="3" y="9" width="4" height="13"/><rect x="10" y="9" width="4" height="13"/><rect x="17" y="9" width="4" height="13"/><rect x="24" y="9" width="4" height="13"/><rect x="0" y="23" width="30" height="4"/></svg></div>
  <div class="offer-name heading">Large Offices</div>
  <p class="offer-text">Lorem ipsum dolor sit amet, consectetur adipiscing elit, sed do eiusmod tempor incididunt ut labore et dolore magna aliqua. Ut enim ad minim veniam, quis nostrud exercitation ullamco laboris nisi ut aliquip ex ea commodo consequat.</p>
  <div class="read-more">Read More</div>
</div>

<div class="abs offer-card" style="left:466px">
  <div class="offer-photo" role="img" aria-label="City skyline of condominium towers at dusk" style="background:linear-gradient(180deg,#6f8fb4,#c49a86 45%,#4e5a6e 100%)"></div>
  <div class="offer-icon"><svg width="24" height="30" viewBox="0 0 24 30" fill="#fff"><path d="M0 0h24v30H14v-6h-4v6H0z"/><g fill="#0d2f55"><rect x="4" y="4" width="4" height="4"/><rect x="10" y="4" width="4" height="4"/><rect x="16" y="4" width="4" height="4"/><rect x="4" y="11" width="4" height="4"/><rect x="10" y="11" width="4" height="4"/><rect x="16" y="11" width="4" height="4"/><rect x="4" y="18" width="4" height="4"/><rect x="16" y="18" width="4" height="4"/></g></svg></div>
  <div class="offer-name heading">Condominiums</div>
  <p class="offer-text">Lorem ipsum dolor sit amet, consectetur adipiscing elit, sed do eiusmod tempor incididunt ut labore et dolore magna aliqua. Ut enim ad minim veniam, quis nostrud exercitation ullamco laboris nisi ut aliquip ex ea commodo consequat.</p>
  <div class="read-more">Read More</div>
</div>

<div class="abs offer-card" style="left:758px">
  <div class="offer-photo" role="img" aria-label="Engineers in hard hats beside industrial machinery" style="background:linear-gradient(150deg,#9fb2c6,#5d7188 50%,#2c3a4c)"></div>
  <div class="offer-icon"><svg width="30" height="26" viewBox="0 0 30 26" fill="#fff"><path d="M10 0h10v5h-2V2h-6v3h-2z"/><rect x="0" y="5" width="30" height="21" rx="2"/><rect x="0" y="13" width="30" height="2" fill="#0d2f55"/><rect x="13" y="11" width="4" height="6" fill="#fff" stroke="#0d2f55"/></svg></div>
  <div class="offer-name heading">Industrial Projects</div>
  <p class="offer-text">Lorem ipsum dolor sit amet, consectetur adipiscing elit, sed do eiusmod tempor incididunt ut labore et dolore magna aliqua. Ut enim ad minim veniam, quis nostrud exercitation ullamco laboris nisi ut aliquip ex ea commodo consequat.</p>
  <div class="read-more">Read More</div>
</div>

<h2 class="abs section-title title-provide heading">What We Provide</h2>

<div class="abs service" style="left:175px">
  <div class="service-photo" role="img" aria-label="Commercial plumbing pipework in a plant room" style="background:linear-gradient(135deg,#1c3450,#5f86ad 45%,#a9c4dc 60%,#27425f)">
    <div class="service-label heading">Commercial<br>Plumbing</div>
  </div>
  <p class="service-text">Lorem ipsum dolor sit amet, consectetur adipiscing elit, sed do eiusmod tempor incididunt ut labore et dolore magna aliqua. Ut enim ad minim veniam, quis nostrud exercitation ullamco laboris ...</p>
</div>

<div class="abs service" style="left:614px">
  <div class="service-photo" role="img" aria-label="Wrenches and pipe fittings laid on technical plans" style="background:linear-gradient(135deg,#d9dcdf,#f2f3f4 45%,#b3b8bd)">
    <div class="service-label heading">Mechanical<br>Contractor</div>
  </div>
  <p class="service-text">Lorem ipsum dolor sit amet, consectetur adipiscing elit, sed do eiusmod tempor incididunt ut labore et dolore magna aliqua. Ut enim ad minim veniam, quis nostrud exercitation ullamco laboris ...</p>
</div>

<section class="abs testimonials" role="img" aria-label="Plumber at work under a sink, tinted blue"></section>
<h2 class="abs testimonials-title heading">Testimonials</h2>
<svg class="abs arrow" style="left:80px" width="16" height="26" viewBox="0 0 16 26"><path d="M13 3 4 13l9 10" fill="none" stroke="#fff" stroke-width="3"/></svg>
<svg class="abs arrow" style="left:1104px" width="16" height="26" viewBox="0 0 16 26"><path d="M3 3l9 10-9 10" fill="none" stroke="#fff" stroke-width="3"/></svg>
<div class="abs client-photo" role="img" aria-label="Portrait of a client"></div>
<div class="abs quote">
  <svg width="40" height="32" viewBox="0 0 40 32" fill="#0392cd"><path d="M0 32V18C0 8 5 2 15 0v6c-5 2-7 5-7 10h7v16zM22 32V18c0-10 5-16 15-18v6c-5 2-7 5-7 10h7v16z"/></svg>
  <span class="quote-name">Daniel Porter</span>
</div>
<p class="abs quote-text">Sed ut perspiciatis unde omnis iste natus error sit voluptatem accusantium doloremque laudantium, totam rem aperiam, eaque ipsa quae ab illo inventore veritatis et quasi architecto beatae vitae dicta sunt explicabo. Nemo enim ipsam voluptatem quia voluptas sit aspernatur aut odit aut fugit, sed quia consequuntur magni dolores eos qui ratione</p>

<div class="abs brand footer-brand">
  <span class="brand-dot"></span>
  <span class="brand-name">Harlow<br>Mechanical<br>Contractors</span>
</div>
<ul class="abs footer-list" style="left:454px">
  <li>› Home</li><li>› About Us</li><li>› Services</li><li>› Clients</li><li>› Testimonials</li><li>› Contact Us</li>
</ul>
<ul class="abs footer-list" style="left:616px">
  <li>› Terms of Service</li><li>› Privacy Policy</li><li>› Help Cookies</li>
</ul>
<ul class="abs footer-list" style="left:784px">
  <li>› Werkstattbüro</li><li class="indent">Lindenstraße 42</li><li class="indent">10969 Berlin | Germany</li><li>› Telephone: +49 30 55501842</li><li>› E-mail: info@harlowmech.example</li>
</ul>
<div class="abs footer-bar">© 2016 Company Name | All Rights Reserved</div>

</body>
</html>
```